International Woodworking Brand needs new site

Our Website has not been revamped for a long time.. The imaging and construction are now tired and dated. Its clumsy and cumbersome to edit, uses outdated software. The site can only be edited and updated from NZ. We need multiple editors worldwide refreshing our content, within prescribed templates to maintain look and feel. We want to use a Wordpress platform.

KELBRO is the main brand of the Forvane Industries. Traditionally, the website is branded with Forvane, the company name. This is incorrect now and needs a shift to our KELBRO brand. Also new levels of service and functionality are required.

KELBRO has a strong reputation in the market place for innovation and leading edge technology in it's field. We have also worked hard to develop a reputation for excellent customer service. Our website also needs to reflect and reinforce these concepts.

We want a fresh, clean, modern site that meets all best practices of SEO marketing, is easy for our customers to navigate and use, and reinforces our brand reputation and our product sales.

See the attached Brief for more specifics.

Target Market(s)

End Users - Woodworkers
Dealers/Stores
Forvane Employees

More demographic and customer profile info is available on request

Industry/Entity Type

Woodworking

Coding

Coded - Design and coding required

Font styles to use
Sans Serif

Colors
ec1f27

Requirements
Must have
• See the brief attached
Nice to have
• See the brief attached
Should not have
• See the brief attached

```html
<!DOCTYPE html>
<html lang="en">
<head>
<meta charset="utf-8">
<title>Forvane Industries</title>
<link href="https://fonts.googleapis.com/css2?family=Raleway:wght@500;600;700&family=Open+Sans:wght@400;600;700&display=swap" rel="stylesheet">
<style>
:root{
  --red:#c4050c;
  --red-bright:#ec1f27;
  --black:#000;
  --white:#fff;
  --ink:#111;
  --grey:#c4c4c4;
  --muted:#555;
  --link:#ddd;
}
*{margin:0;padding:0;box-sizing:border-box}
html,body{width:675px;height:1200px;overflow:hidden;background:var(--white)}
body{position:relative;font-family:'Open Sans',sans-serif;color:var(--ink)}
.abs{position:absolute}

.header{top:0;left:0;width:675px;height:60px;background:var(--white)}
.brand{left:78px;top:17px;display:flex;align-items:center;gap:7px;font-family:'Raleway',sans-serif;font-weight:700;font-size:17px;color:var(--ink)}
.brand i{width:20px;height:20px;border-radius:50%;background:var(--red)}
.lang{left:502px;top:21px;width:66px;height:18px;border:1px solid #ddd;border-radius:9px;font-size:6.5px;color:#777;padding:4px 0 0 9px}
.lang b{position:absolute;right:15px;top:5px;width:10px;height:7px;background:#2a3f8f}
.lang .caret{position:absolute;right:6px;top:4px;font-size:5px;color:#333}
.search{left:575px;top:20px;width:20px;height:20px;border-radius:50%;background:#eee}

.nav{top:60px;left:0;width:675px;height:29px;background:var(--red);display:flex;padding-left:102px}
.nav a{color:var(--white);font-size:7px;font-weight:700;line-height:29px;padding:0 10.4px;text-decoration:none}
.nav a.on{background:var(--black);padding:0 13px}

.hero{top:89px;left:0;width:675px;height:329px;
  background:
    linear-gradient(rgba(0,0,0,.15),rgba(0,0,0,.45)),
    radial-gradient(ellipse 30% 45% at 78% 30%,rgba(150,120,95,.55),transparent 70%),
    radial-gradient(ellipse 35% 40% at 28% 45%,rgba(120,85,55,.6),transparent 70%),
    radial-gradient(ellipse 40% 35% at 55% 85%,rgba(70,80,70,.5),transparent 70%),
    linear-gradient(100deg,#2a2d2c 0%,#4a3f35 40%,#3a3630 70%,#1e1f20 100%)}
.hero h1{position:absolute;top:155px;width:100%;text-align:center;color:var(--white);font-family:'Raleway',sans-serif;font-weight:600;font-size:21px;line-height:25px}
.btn{display:block;background:var(--red);color:var(--white);border-radius:14px;font-size:7.5px;font-weight:600;text-align:center;line-height:26px;width:89px;text-decoration:none}
.hero .btn{position:absolute;left:293px;top:219px}
.dots{position:absolute;left:319px;top:291px;display:flex;gap:4px}
.dots span{width:6px;height:6px;border:1px solid var(--white);border-radius:50%}
.dots span.on{border-color:var(--red-bright)}

.title{width:100%;text-align:center;font-family:'Raleway',sans-serif;font-weight:600;font-size:16.5px}
.about-title{top:428px;left:0}
.about-text{top:458px;left:103px;width:469px;text-align:center;font-size:8px;line-height:11px;color:#222}
.brandmark{top:499px;left:0;width:675px;text-align:center;font-family:'Raleway',sans-serif;font-weight:700;font-size:27px;color:#9a9a9a;letter-spacing:1px}
.about-btn{top:547px;left:293px}

.products{top:583px;left:0;width:675px;height:295px;background:var(--black)}
.products .title{color:var(--white);position:absolute;top:11px}
.tile{position:absolute;width:174px;height:118px;
  background:
    radial-gradient(ellipse 38% 42% at 55% 38%,rgba(120,120,125,.55),transparent 75%),
    linear-gradient(#fff 0%,#f0f0f0 35%,#b8b8b8 62%,#2a2a2a 85%,#000 100%)}
.tile.dark{background:
    radial-gradient(ellipse 45% 45% at 45% 40%,rgba(200,200,205,.6),transparent 75%),
    linear-gradient(#6f6f72 0%,#404044 55%,#111 85%,#000 100%)}
.tile.warm{background:
    radial-gradient(ellipse 30% 40% at 55% 40%,rgba(60,70,90,.55),transparent 75%),
    linear-gradient(#a07c58 0%,#7a5b3e 45%,#3a2a1c 78%,#000 100%)}
.tile.grind{background:
    radial-gradient(ellipse 25% 35% at 65% 40%,rgba(215,210,190,.7),transparent 75%),
    radial-gradient(ellipse 30% 30% at 35% 45%,rgba(200,120,95,.55),transparent 75%),
    linear-gradient(#5a4a3c 0%,#3f352c 55%,#141210 82%,#000 100%)}
.tile span{position:absolute;bottom:8px;right:12px;color:var(--white);font-family:'Raleway',sans-serif;font-weight:600;font-size:10.5px}

.news-title{top:888px;left:0}
.news{position:absolute;top:928px;width:192px}
.date{position:absolute;left:-50px;top:0;width:43px;height:43px;border-radius:50%;background:var(--grey);text-align:center;font-family:'Raleway',sans-serif;font-weight:700;font-size:13px;line-height:14px;padding-top:8px}
.date small{display:block;font-size:8.5px;font-weight:600}
.news h3{font-family:'Raleway',sans-serif;font-weight:700;font-size:9.5px;line-height:11.5px}
.news p{font-size:6.3px;line-height:10.5px;color:var(--muted);margin-top:3px;text-align:justify}
.meta{display:flex;gap:14px;font-size:5.5px;font-weight:700;margin-top:9px;align-items:center}
.meta span{display:flex;align-items:center;gap:7px}

.footer{top:1047px;left:0;width:675px;height:131px;background:var(--black)}
.footer-head{color:var(--red);font-family:'Raleway',sans-serif;font-weight:700;font-size:11px}
.links{position:absolute;list-style:none;font-size:7px;color:var(--link);line-height:16.2px}
.links li::before{content:"›";margin-right:8px}
.email{position:absolute;left:432px;top:1087px;width:145px;height:20px;background:var(--white);border-radius:10px;font-size:5.5px;padding:6px 0 0 11px}
.email svg{position:absolute;right:11px;top:6px}
.sub{position:absolute;left:432px;top:1111px;width:145px;height:20px;background:var(--red);border-radius:10px;color:var(--white);font-weight:600;font-size:10.5px;text-align:center;line-height:20px}
.social{position:absolute;left:462px;top:1141px;display:flex;gap:11px}
.bottom{top:1178px;left:0;width:675px;height:22px;background:var(--red);color:var(--white);font-size:5.5px;text-align:center;line-height:22px}
</style>
</head>
<body>
<header class="abs header">
  <div class="abs brand"><i></i>Forvane</div>
  <div class="abs lang">English<b></b><span class="caret">▼</span></div>
  <div class="abs search"><svg width="20" height="20" viewBox="0 0 20 20"><circle cx="9" cy="9" r="3.5" fill="none" stroke="#111" stroke-width="1.6"/><line x1="11.6" y1="11.6" x2="14" y2="14" stroke="#111" stroke-width="1.8"/></svg></div>
</header>
<nav class="abs nav">
  <a class="on">HOME</a><a>PRODUCTS</a><a>SUPPORT</a><a>WHERE TO BUY</a><a>REGISTER YOUR WARRANTY</a><a>ABOUT</a><a>CONTACT US</a>
</nav>
<section class="abs hero" role="img" aria-label="Woodworker operating a metal lathe in a dim workshop">
  <h1>Consequuntur magni dolores eos<br>qui ratione voluptatem</h1>
  <a class="btn">LEARN MORE</a>
  <div class="dots"><span></span><span class="on"></span><span></span><span></span></div>
</section>
<h2 class="abs title about-title">ABOUT FORVANE</h2>
<p class="abs about-text">sed do eiusmod tempor incididunt ut labore et dolore magna aliqua. Ut enim ad minim veniam, quis nostrud exercitation ullamco laboris nisi ut aliquip ex ea commodo consequat. Duis aute irure dolor in reprehenderit in voluptate velit esse cillum dolore eu fugiat nulla pariatur.</p>
<div class="abs brandmark">KELBRO</div>
<a class="abs btn about-btn">READ MORE</a>
<section class="abs products">
  <h2 class="title">PRODUCTS</h2>
  <div class="tile" style="left:75px;top:37px" role="img" aria-label="Wood lathe"><span>LATHES</span></div>
  <div class="tile" style="left:251px;top:37px" role="img" aria-label="Drill chuck with key"><span>LATHE ACCESSORIES</span></div>
  <div class="tile" style="left:427px;top:37px" role="img" aria-label="Four-jaw chuck"><span>CHUCKS</span></div>
  <div class="tile dark" style="left:75px;top:157px" role="img" aria-label="Chuck jaws close-up"><span>CHUCK ACCESSORIES</span></div>
  <div class="tile warm" style="left:251px;top:157px" role="img" aria-label="Woodworker in a workshop"><span>WORKSHOP</span></div>
  <div class="tile grind" style="left:427px;top:157px" role="img" aria-label="Hands sharpening a tool on a grinder"><span>OTHER</span></div>
</section>
<h2 class="abs title news-title">LATEST NEWS</h2>
<article class="news" style="left:138px">
  <div class="date">02<small>AUG</small></div>
  <h3>EXCEPTEUR SINT OCCAECAT CUPIDATAT NON PROIDENT,</h3>
  <p>Duis aute irure dolor in reprehenderit in voluptate velit esse cillum dolore eu fugiat nulla pariatur. Excepteur sint occaecat cupidatat non proident,</p>
  <div class="meta">
    <span><svg width="8" height="7" viewBox="0 0 8 7"><ellipse cx="4" cy="3" rx="4" ry="2.8" fill="#111"/><path d="M1.5 5 L1 7 L3.5 5.5Z" fill="#111"/></svg>COMMENTS : 20</span>
    <span><svg width="7" height="7" viewBox="0 0 7 7"><circle cx="3.5" cy="3.5" r="2.9" fill="none" stroke="#111" stroke-width="1"/><path d="M3.5 1.8V3.6H5" fill="none" stroke="#111" stroke-width=".8"/></svg>2 HOURS AGO</span>
  </div>
</article>
<article class="news" style="left:397px">
  <div class="date">02<small>AUG</small></div>
  <h3>EXCEPTEUR SINT OCCAECAT CUPIDATAT NON PROIDENT,</h3>
  <p>Duis aute irure dolor in reprehenderit in voluptate velit esse cillum dolore eu fugiat nulla pariatur. Excepteur sint occaecat cupidatat non proident,</p>
  <div class="meta">
    <span><svg width="8" height="7" viewBox="0 0 8 7"><ellipse cx="4" cy="3" rx="4" ry="2.8" fill="#111"/><path d="M1.5 5 L1 7 L3.5 5.5Z" fill="#111"/></svg>COMMENTS : 20</span>
    <span><svg width="7" height="7" viewBox="0 0 7 7"><circle cx="3.5" cy="3.5" r="2.9" fill="none" stroke="#111" stroke-width="1"/><path d="M3.5 1.8V3.6H5" fill="none" stroke="#111" stroke-width=".8"/></svg>2 HOURS AGO</span>
  </div>
</article>
<footer class="abs footer"></footer>
<h4 class="abs footer-head" style="left:97px;top:1062px">QUICK LINKS</h4>
<ul class="links" style="left:97px;top:1083px"><li>Home</li><li>Products</li><li>Support</li><li>Where to Buy</li><li>Register Your Warranty</li></ul>
<ul class="links" style="left:216px;top:1083px"><li>About</li><li>Contact</li><li>Terms and Conditions</li><li>Privacy Policy</li></ul>
<h4 class="abs footer-head" style="left:434px;top:1062px">NEWSLETTER SUBSCRIBE</h4>
<div class="email">ENTER EMAIL ID<svg width="7" height="5" viewBox="0 0 7 5"><rect width="7" height="5" fill="#555"/><path d="M0 0L3.5 2.8L7 0" fill="none" stroke="#fff" stroke-width=".7"/></svg></div>
<div class="sub">SUBSCRIBE</div>
<div class="social" aria-label="Social links">
  <svg width="13" height="13" viewBox="0 0 13 13" aria-label="Share"><circle cx="3" cy="6.5" r="2" fill="#fff"/><circle cx="10" cy="2.5" r="2" fill="#fff"/><circle cx="10" cy="10.5" r="2" fill="#fff"/><path d="M3 6.5L10 2.5M3 6.5L10 10.5" stroke="#fff" stroke-width="1.2"/></svg>
  <svg width="13" height="13" viewBox="0 0 13 13" aria-label="Chat"><path d="M1 2h11v7H5l-3 3V9H1z" fill="#fff"/></svg>
  <svg width="13" height="13" viewBox="0 0 13 13" aria-label="Website"><circle cx="6.5" cy="6.5" r="5.5" fill="none" stroke="#fff" stroke-width="1.3"/><path d="M1 6.5h11M6.5 1c-3 3-3 8 0 11M6.5 1c3 3 3 8 0 11" fill="none" stroke="#fff" stroke-width="1"/></svg>
  <svg width="13" height="13" viewBox="0 0 13 13" aria-label="Video"><rect x="0.5" y="2" width="12" height="9" rx="2" fill="#fff"/><path d="M5 4.5v4l3.5-2z" fill="#000"/></svg>
</div>
<div class="abs bottom">© 2016, www.forvane-site.com | All rights reserved</div>
</body>
</html>
```